Social Media App Needs PPT Template

We need a PowerPoint template for a new social media company based in the DC area called "Bold Ledger." We provide an interactive digital platform for executives to share actionable advice. We would like to see designs that use our orange logo color as an accent, but are mainly grey, white, and black. The final design should communicate clean, chic, modern, and professional.

Target Market(s)

Executives

Industry/Entity Type

Information Technology

Font styles to use
Sans Serif

Colors
f78f20
fbe7d2
ffffff
000000
e8e8e8
757575

Requirements
Must have
• My project must have title page and many options for the body of the ppt (graphs, tables, etc). It also needs to be easy to modify. I must have someone who is experienced in creating powerpoint templates.
Nice to have
• It would be nice to have a very modern and clean design that includes the logo on every page, but still leaves a lot of room for the content of the slide
Should not have
• My design project should not look to busy.

```html
<!DOCTYPE html>
<html lang="en">
<head>
<meta charset="UTF-8">
<title>Bold Ledger – Three Column Slide</title>
<link rel="stylesheet" href="https://fonts.googleapis.com/css2?family=Lato:wght@300;400;700&family=Oswald:wght@500&display=swap">
<style>
  :root {
    --stage: #555555;
    --paper: #ffffff;
    --ink: #232f3e;
    --accent: #f78f20;
    --body-text: #2b2b2b;
    --muted: #757575;
    --label: #e8e8e8;
  }
  * { margin: 0; padding: 0; box-sizing: border-box; }
  html, body { width: 1200px; height: 960px; overflow: hidden; }
  body {
    background: var(--stage);
    font-family: "Lato", sans-serif;
    position: relative;
  }
  .page-label {
    position: absolute;
    top: 74px; left: 0; width: 1200px;
    text-align: center;
    color: var(--label);
    font-weight: 300;
    font-size: 26px;
  }
  .slide {
    position: absolute;
    left: 123px; top: 159px;
    width: 987px; height: 741px;
    background: var(--paper);
  }
  .accent-stripe {
    position: absolute; left: 0; top: 15px;
    width: 100%; height: 11px;
    background: var(--accent);
  }
  .title-band {
    position: absolute; left: 0; top: 29px;
    width: 100%; height: 95px;
    background: var(--ink);
    display: flex; align-items: center; justify-content: space-between;
    padding: 0 44px 0 42px;
  }
  .slide-title {
    font-family: "Oswald", sans-serif;
    font-weight: 500;
    font-size: 46px;
    letter-spacing: -1px;
    color: var(--paper);
    text-transform: uppercase;
  }
  .brand { display: flex; align-items: center; gap: 10px; }
  .brand-dot { width: 14px; height: 14px; border-radius: 50%; background: var(--accent); }
  .brand-name {
    font-family: "Lato", sans-serif;
    font-weight: 700;
    font-size: 24px;
    color: var(--paper);
  }
  .feature {
    position: absolute; top: 236px;
    width: 258px;
  }
  .feature-icon { display: block; height: 110px; margin: 0 auto; }
  .feature-text {
    margin-top: 20px;
    font-size: 17.5px;
    line-height: 25.2px;
    color: var(--body-text);
    text-align: justify;
    text-align-last: center;
    hyphens: manual;
  }
  .feature--growth { left: 45px; }
  .feature--partner { left: 365px; }
  .feature--approval { left: 681px; }
  .footer-rule {
    position: absolute; left: 664px; top: 684px;
    width: 285px; height: 1px; background: var(--muted);
  }
  .footer-meta {
    position: absolute; right: 35px; top: 701px;
    font-size: 13.5px; color: var(--muted);
  }
</style>
</head>
<body>
  <div class="page-label">Page 5</div>

  <section class="slide">
    <div class="accent-stripe"></div>
    <header class="title-band">
      <h1 class="slide-title">Title Goes Here</h1>
      <div class="brand">
        <span class="brand-dot"></span>
        <span class="brand-name">Bold Ledger</span>
      </div>
    </header>

    <article class="feature feature--growth">
      <svg class="feature-icon" viewBox="0 0 140 110" width="140" height="110" fill="none" stroke="var(--ink)" stroke-width="5" stroke-linejoin="round" stroke-linecap="round">
        <rect x="8" y="6" width="124" height="86" rx="3"/>
        <rect x="20" y="18" width="100" height="62"/>
        <rect x="3" y="92" width="134" height="12" rx="2"/>
        <polyline points="36,62 56,46 74,56 96,38"/>
      </svg>
      <p class="feature-text">Duis autem vel eum iriure dolor in hendrerit in vulputate velit esse molestie consequat, vel illum dolore eu feugiat nulla facilisis at vero eros et accumsan et iusto odio dignissim qui blan&shy;dit praesent luptatum zzril del enit augue duis dolore te feugait nulla facilisi.</p>
    </article>

    <article class="feature feature--partner">
      <svg class="feature-icon" viewBox="0 0 140 110" width="140" height="110" fill="none" stroke="var(--accent)" stroke-width="5" stroke-linejoin="round" stroke-linecap="round">
        <rect x="4" y="18" width="22" height="34" rx="2" transform="rotate(-45 15 35)"/>
        <rect x="114" y="18" width="22" height="34" rx="2" transform="rotate(45 125 35)"/>
        <path d="M30 40 L44 30 L66 34 L52 46 Q60 52 70 44 L84 36"/>
        <path d="M110 40 L96 30 L80 30"/>
        <path d="M28 52 L48 78 Q58 92 70 96 Q80 92 90 82 L112 54"/>
        <circle cx="42" cy="70" r="5"/>
        <circle cx="50" cy="80" r="5"/>
        <circle cx="60" cy="88" r="5"/>
        <circle cx="70" cy="94" r="5"/>
        <path d="M72 62 L90 78 M80 56 L98 70"/>
      </svg>
      <p class="feature-text">Duis autem vel eum iriure dolor in hendrerit in vulputate velit esse molestie consequat, vel illum dolore eu feugiat nulla facilisis at vero eros et accumsan et iusto odio dignissim qui blan&shy;dit praesent luptatum zzril dele nit augue duis dolore te feugait nulla facilisi.</p>
    </article>

    <article class="feature feature--approval">
      <svg class="feature-icon" viewBox="0 0 140 110" width="140" height="110" fill="none" stroke="var(--ink)" stroke-width="5" stroke-linejoin="round" stroke-linecap="round">
        <rect x="22" y="46" width="12" height="42" rx="1"/>
        <rect x="34" y="42" width="14" height="50" rx="2"/>
        <path d="M48 50 L64 38 L76 18 Q80 8 88 12 Q94 16 90 30 L86 44 L108 44 Q116 46 114 54 Q112 58 108 60 Q114 64 110 70 Q106 74 104 74 Q108 80 102 84 Q98 86 96 86 Q98 94 90 96 L60 96 L48 88"/>
        <path d="M94 60 L108 60 M94 74 L104 74"/>
      </svg>
      <p class="feature-text">Duis autem vel eum iriure dolor in hendrerit in vulputate velit esse molestie consequat, vel illum dolore eu feugiat nulla facilisis at vero eros et accumsan et iusto odio dignissim qui blan&shy;dit praesent luptatum zzril del enit augue duis dolore te feugait nulla facilisi.</p>
    </article>

    <div class="footer-rule"></div>
    <p class="footer-meta">www.boldledger.com &nbsp;|&nbsp; Page 3</p>
  </section>
</body>
</html>
```